Homemaking training schools needs a Business Card design

Designer, Hello!

No special requirements, good-looking enough.
--------------------------------------------------------------------------

Name: Marcus Dole
Chairman
Tel: 0574-71948263
Mobile: 13857420916
Email: kelvora@mailnest.example
Web: www.prt2019.example
Add: No.258, LanpingJie, BeiyuanQu, Ningbo, Zhejiang

LOGO
Ningbo PRT Homemaking Training School

Target Market(s)

pregnant women, mothers, infants, the elderly and families, including cleaning, cooking, nursing training.

Industry/Entity Type

Business

Contact Information for Business Card

Name: Marcus Dole
Chairman
Tel: 0574-71948263
Mobile: 13857420916
Email: kelvora@mailnest.example
Web: www.prt2019.example

LOGO

Font styles to use
Serif
Sans Serif
Decorative

Requirements
Nice to have
• Feels: clean, specifications, safety, comfort, warmth and happiness.

```html
<!DOCTYPE html>
<html lang="en">
<head>
<meta charset="utf-8">
<title>PingRuiTang Business Card</title>
<link href="https://fonts.googleapis.com/css2?family=Montserrat:wght@500;600;700&display=swap" rel="stylesheet">
<style>
  :root {
    --canvas: #2b2b2d;
    --card: #000000;
    --blue: #1a7fd0;
    --pink: #ec0f8c;
    --white: #ffffff;
  }
  * { margin: 0; padding: 0; box-sizing: border-box; }
  html, body { width: 1200px; height: 900px; overflow: hidden; background: var(--canvas); }
  body { position: relative; font-family: "Montserrat", sans-serif; }

  .card {
    position: absolute;
    width: 620px; height: 354px;
    background: var(--card);
    overflow: hidden;
    box-shadow: 0 10px 30px rgba(0,0,0,.45);
  }
  .card--front { left: 120px; top: 60px; }
  .card--back { left: 460px; top: 486px; }
  .card__shapes { position: absolute; inset: 0; }

  .brand-name {
    position: absolute;
    color: var(--blue); font-weight: 600; line-height: 1; white-space: nowrap;
  }
  .card--front .brand-name { left: 0; right: 0; top: 132px; text-align: center; font-size: 54px; }
  .card--back .brand-name { left: 44px; top: 62px; font-size: 38px; }

  .front__web {
    position: absolute; left: 26px; bottom: 9px;
    color: var(--white); font-size: 17px; font-weight: 600; letter-spacing: .3px;
  }

  .person { position: absolute; right: 34px; top: 64px; text-align: right; }
  .person__title { color: var(--white); font-size: 11px; font-weight: 600; letter-spacing: 1px; }
  .person__name { color: var(--blue); font-size: 27px; font-weight: 700; letter-spacing: .5px; line-height: 1.05; }

  .address {
    position: absolute; right: 16px; top: 196px; text-align: right;
    color: var(--white); font-size: 13px; font-weight: 500; line-height: 1.35;
  }

  .contacts { position: absolute; left: 38px; top: 196px; list-style: none; }
  .contacts li {
    display: flex; align-items: center; gap: 10px;
    color: var(--white); font-size: 15px; font-weight: 600; line-height: 21px;
  }
  .contacts svg { width: 12px; height: 12px; flex: none; }
</style>
</head>
<body>

  <section class="card card--front" aria-label="Business card front">
    <svg class="card__shapes" viewBox="0 0 620 354" aria-hidden="true">
      <polygon points="0,312 232,312 256,354 0,354" fill="var(--blue)"/>
      <polygon points="236,318 620,318 620,334 246,334" fill="var(--pink)"/>
    </svg>
    <div class="brand-name">PingRuiTang</div>
    <div class="front__web">www.prt2019.example</div>
  </section>

  <section class="card card--back" aria-label="Business card back">
    <svg class="card__shapes" viewBox="0 0 620 354" aria-hidden="true">
      <line x1="30" y1="176" x2="596" y2="176" stroke="var(--blue)" stroke-width="2"/>
      <polygon points="422,186 620,186 620,240 404,240" fill="var(--blue)"/>
      <polygon points="0,298 390,298 402,250 414,250 400,314 0,314" fill="var(--pink)"/>
    </svg>
    <div class="brand-name">PingRuiTang</div>
    <div class="person">
      <div class="person__title">CHAIRMAN</div>
      <div class="person__name">MARCUS DOLE</div>
    </div>
    <div class="address">258, LanpingJie<br>BeiyuanQu, Ningbo, Zhejiang</div>
    <ul class="contacts">
      <li>
        <svg viewBox="0 0 12 12" aria-hidden="true"><path d="M2 1l2 0 1 3-1.3 1a7 7 0 0 0 3.3 3.3L8 7l3 1v2a1 1 0 0 1-1 1A9 9 0 0 1 1 2a1 1 0 0 1 1-1z" fill="var(--white)"/></svg>
        0574-71948263
      </li>
      <li>
        <svg viewBox="0 0 12 12" aria-hidden="true"><rect x="3" y="0.8" width="6" height="10.4" rx="1" fill="none" stroke="var(--white)" stroke-width="1.4"/><circle cx="6" cy="9.3" r=".7" fill="var(--white)"/></svg>
        13857420916
      </li>
      <li>
        <svg viewBox="0 0 12 12" aria-hidden="true"><rect x="0.8" y="2.5" width="10.4" height="7" fill="none" stroke="var(--white)" stroke-width="1.2"/><path d="M1 3l5 4 5-4" fill="none" stroke="var(--white)" stroke-width="1.2"/></svg>
        kelvora@mailnest.example
      </li>
      <li>
        <svg viewBox="0 0 12 12" aria-hidden="true"><circle cx="6" cy="6" r="5" fill="none" stroke="var(--white)" stroke-width="1.1"/><ellipse cx="6" cy="6" rx="2.2" ry="5" fill="none" stroke="var(--white)" stroke-width="1"/><line x1="1" y1="6" x2="11" y2="6" stroke="var(--white)" stroke-width="1"/></svg>
        www.prt2019.example
      </li>
    </ul>
  </section>

</body>
</html>
```